Kettleby Twins Playing Cards

We are wanting a cool design for a playing card that includes our logo(s). I will attach our two logos, we are open to using either one of them or another version of them. I will also attach some pictures of card decks to use for inspiration. These are just decks that we have seen from other artists that we liked. We are located in West Texas so although not necessary, a Sotol or Agave or cactus or quail (bird) or some sort of sunset would pay homage to our surroundings. I realize the examples are all very different, but those are just some decks that we like! Thank you!

```html
<!DOCTYPE html>
<html lang="en">
<head>
<meta charset="utf-8">
<title>Kettleby Twins Playing Cards – Deck Layout</title>
<link rel="stylesheet" href="https://fonts.googleapis.com/css2?family=Roboto+Slab:wght@700&display=swap">
<style>
:root{
  --page:#ffffff;
  --card:#060709;
  --frame:#b48a3a;
  --frame-light:#e2c57c;
  --red:#d81f26;
  --red-dark:#8e1016;
  --gold:#e6c882;
  --gold-dark:#a77b2c;
  --ink:#2a1a05;
}
*{box-sizing:border-box;margin:0;padding:0}
html,body{width:1200px;height:555px;overflow:hidden;background:var(--page)}
body{position:relative;font-family:"Roboto Slab",Georgia,serif}
.deck{position:absolute;left:17.7px;display:grid;grid-template-columns:repeat(14,71.3px);column-gap:12.8px;row-gap:17px}
.deck-top{top:34px}
.deck-bottom{top:305px}
.card{position:relative;width:71.3px;height:100px;background:var(--card);border:1px solid var(--frame);border-radius:2px;box-shadow:inset 0 0 0 2px var(--card),inset 0 0 0 2.6px var(--frame-light);overflow:hidden}
.hearts,.diamonds{--suit:var(--red)}
.spades,.clubs{--suit:var(--gold)}
.idx{position:absolute;left:5px;top:4px;display:flex;flex-direction:column;align-items:center;font-size:11px;line-height:10px;color:var(--suit);letter-spacing:-0.5px}
.idx b{font-size:7px;line-height:8px;font-family:"Segoe UI Symbol","DejaVu Sans",sans-serif}
.idx.flip{left:auto;top:auto;right:5px;bottom:4px;transform:rotate(180deg)}
.pips i{position:absolute;left:var(--x);top:var(--y);transform:translate(-50%,-50%) rotate(var(--r,0deg));font-style:normal;font-size:14px;line-height:1;color:var(--suit);font-family:"Segoe UI Symbol","DejaVu Sans",sans-serif}
.r2 i:nth-child(1),.r3 i:nth-child(1){--x:50%;--y:14%}
.r2 i:nth-child(2),.r3 i:nth-child(3){--x:50%;--y:84%;--r:180deg}
.r3 i:nth-child(2),.r5 i:nth-child(5),.r9 i:nth-child(9){--x:50%;--y:50%}
.pips i:nth-child(1){--x:34%;--y:14%}
.pips i:nth-child(2){--x:66%;--y:14%}
.r4 i:nth-child(3),.r5 i:nth-child(3),.r6 i:nth-child(5),.r7 i:nth-child(6),.r8 i:nth-child(7),.r9 i:nth-child(7),.r10 i:nth-child(7){--x:34%;--y:84%;--r:180deg}
.r4 i:nth-child(4),.r5 i:nth-child(4),.r6 i:nth-child(6),.r7 i:nth-child(7),.r8 i:nth-child(8),.r9 i:nth-child(8),.r10 i:nth-child(8){--x:66%;--y:84%;--r:180deg}
.r6 i:nth-child(3),.r7 i:nth-child(4){--x:34%;--y:49%}
.r6 i:nth-child(4),.r7 i:nth-child(5){--x:66%;--y:49%}
.r7 i:nth-child(3){--x:50%;--y:31%}
.r8 i:nth-child(3),.r9 i:nth-child(3),.r10 i:nth-child(3){--x:34%;--y:38%}
.r8 i:nth-child(4),.r9 i:nth-child(4),.r10 i:nth-child(4){--x:66%;--y:38%}
.r8 i:nth-child(5),.r9 i:nth-child(5),.r10 i:nth-child(5){--x:34%;--y:62%;--r:180deg}
.r8 i:nth-child(6),.r9 i:nth-child(6),.r10 i:nth-child(6){--x:66%;--y:62%;--r:180deg}
.r10 i:nth-child(9){--x:50%;--y:27%}
.r10 i:nth-child(10){--x:50%;--y:74%;--r:180deg}
.art{position:absolute;left:50%;top:50%;transform:translate(-50%,-50%)}
.ace-art{width:40px;height:44px;border-radius:45%;background:radial-gradient(circle,var(--suit) 0%,var(--suit) 40%,transparent 72%);opacity:.85}
.face-art{width:46px;height:82px;border-radius:3px;background:linear-gradient(180deg,var(--suit),rgba(0,0,0,.4) 130%);opacity:.75}
.joker-art{width:48px;height:28px;top:48%;border-radius:40% 40% 8px 8px;background:linear-gradient(180deg,var(--suit),rgba(0,0,0,.3) 140%)}
.joker-label{position:absolute;left:5px;top:4px;writing-mode:vertical-rl;text-orientation:upright;font-size:6px;letter-spacing:-1px;color:var(--suit)}
.joker-label.flip{left:auto;top:auto;right:5px;bottom:4px;transform:rotate(180deg)}
.joker-red{--suit:var(--red)}
.joker-gold{--suit:var(--gold)}
.card-back{background:linear-gradient(135deg,var(--gold-dark),var(--gold) 35%,#f1dc9e 50%,var(--gold) 65%,var(--gold-dark));display:flex;align-items:center;justify-content:center}
.brand-name{font-size:5.3px;color:var(--ink);letter-spacing:.1px;white-space:nowrap}
</style>
</head>
<body>
<main class="deck deck-top">
  <!-- hearts -->
  <div class="card joker-red"><span class="joker-label">JOKER</span><span class="joker-label flip">JOKER</span><div class="art joker-art" role="img" aria-label="Red jester hat illustration"></div></div>
  <div class="card hearts"><span class="idx">A<b>&#9829;&#xFE0E;</b></span><span class="idx flip">A<b>&#9829;&#xFE0E;</b></span><div class="art ace-art" role="img" aria-label="Ornate filigree heart"></div></div>
  <div class="card hearts"><span class="idx">K<b>&#9829;&#xFE0E;</b></span><span class="idx flip">K<b>&#9829;&#xFE0E;</b></span><div class="art face-art" role="img" aria-label="Line-art king with sword"></div></div>
  <div class="card hearts"><span class="idx">Q<b>&#9829;&#xFE0E;</b></span><span class="idx flip">Q<b>&#9829;&#xFE0E;</b></span><div class="art face-art" role="img" aria-label="Line-art queen with flower"></div></div>
  <div class="card hearts"><span class="idx">J<b>&#9829;&#xFE0E;</b></span><span class="idx flip">J<b>&#9829;&#xFE0E;</b></span><div class="art face-art" role="img" aria-label="Line-art jack with staff"></div></div>
  <div class="card hearts"><span class="idx">10<b>&#9829;&#xFE0E;</b></span><span class="idx flip">10<b>&#9829;&#xFE0E;</b></span><div class="pips r10"><i>&#9829;&#xFE0E;</i><i>&#9829;&#xFE0E;</i><i>&#9829;&#xFE0E;</i><i>&#9829;&#xFE0E;</i><i>&#9829;&#xFE0E;</i><i>&#9829;&#xFE0E;</i><i>&#9829;&#xFE0E;</i><i>&#9829;&#xFE0E;</i><i>&#9829;&#xFE0E;</i><i>&#9829;&#xFE0E;</i></div></div>
  <div class="card hearts"><span class="idx">9<b>&#9829;&#xFE0E;</b></span><span class="idx flip">9<b>&#9829;&#xFE0E;</b></span><div class="pips r9"><i>&#9829;&#xFE0E;</i><i>&#9829;&#xFE0E;</i><i>&#9829;&#xFE0E;</i><i>&#9829;&#xFE0E;</i><i>&#9829;&#xFE0E;</i><i>&#9829;&#xFE0E;</i><i>&#9829;&#xFE0E;</i><i>&#9829;&#xFE0E;</i><i>&#9829;&#xFE0E;</i></div></div>
  <div class="card hearts"><span class="idx">8<b>&#9829;&#xFE0E;</b></span><span class="idx flip">8<b>&#9829;&#xFE0E;</b></span><div class="pips r8"><i>&#9829;&#xFE0E;</i><i>&#9829;&#xFE0E;</i><i>&#9829;&#xFE0E;</i><i>&#9829;&#xFE0E;</i><i>&#9829;&#xFE0E;</i><i>&#9829;&#xFE0E;</i><i>&#9829;&#xFE0E;</i><i>&#9829;&#xFE0E;</i></div></div>
  <div class="card hearts"><span class="idx">7<b>&#9829;&#xFE0E;</b></span><span class="idx flip">7<b>&#9829;&#xFE0E;</b></span><div class="pips r7"><i>&#9829;&#xFE0E;</i><i>&#9829;&#xFE0E;</i><i>&#9829;&#xFE0E;</i><i>&#9829;&#xFE0E;</i><i>&#9829;&#xFE0E;</i><i>&#9829;&#xFE0E;</i><i>&#9829;&#xFE0E;</i></div></div>
  <div class="card hearts"><span class="idx">6<b>&#9829;&#xFE0E;</b></span><span class="idx flip">6<b>&#9829;&#xFE0E;</b></span><div class="pips r6"><i>&#9829;&#xFE0E;</i><i>&#9829;&#xFE0E;</i><i>&#9829;&#xFE0E;</i><i>&#9829;&#xFE0E;</i><i>&#9829;&#xFE0E;</i><i>&#9829;&#xFE0E;</i></div></div>
  <div class="card hearts"><span class="idx">5<b>&#9829;&#xFE0E;</b></span><span class="idx flip">5<b>&#9829;&#xFE0E;</b></span><div class="pips r5"><i>&#9829;&#xFE0E;</i><i>&#9829;&#xFE0E;</i><i>&#9829;&#xFE0E;</i><i>&#9829;&#xFE0E;</i><i>&#9829;&#xFE0E;</i></div></div>
  <div class="card hearts"><span class="idx">4<b>&#9829;&#xFE0E;</b></span><span class="idx flip">4<b>&#9829;&#xFE0E;</b></span><div class="pips r4"><i>&#9829;&#xFE0E;</i><i>&#9829;&#xFE0E;</i><i>&#9829;&#xFE0E;</i><i>&#9829;&#xFE0E;</i></div></div>
  <div class="card hearts"><span class="idx">3<b>&#9829;&#xFE0E;</b></span><span class="idx flip">3<b>&#9829;&#xFE0E;</b></span><div class="pips r3"><i>&#9829;&#xFE0E;</i><i>&#9829;&#xFE0E;</i><i>&#9829;&#xFE0E;</i></div></div>
  <div class="card hearts"><span class="idx">2<b>&#9829;&#xFE0E;</b></span><span class="idx flip">2<b>&#9829;&#xFE0E;</b></span><div class="pips r2"><i>&#9829;&#xFE0E;</i><i>&#9829;&#xFE0E;</i></div></div>
  <!-- spades -->
  <div class="card card-back" role="img" aria-label="Gold filigree pattern card back"><span class="brand-name">KETTLEBY TWINS</span></div>
  <div class="card spades"><span class="idx">A<b>&#9824;&#xFE0E;</b></span><span class="idx flip">A<b>&#9824;&#xFE0E;</b></span><div class="art ace-art" role="img" aria-label="Ornate filigree spade"></div></div>
  <div class="card spades"><span class="idx">K<b>&#9824;&#xFE0E;</b></span><span class="idx flip">K<b>&#9824;&#xFE0E;</b></span><div class="art face-art" role="img" aria-label="Line-art king with sword"></div></div>
  <div class="card spades"><span class="idx">Q<b>&#9824;&#xFE0E;</b></span><span class="idx flip">Q<b>&#9824;&#xFE0E;</b></span><div class="art face-art" role="img" aria-label="Line-art queen with flower"></div></div>
  <div class="card spades"><span class="idx">J<b>&#9824;&#xFE0E;</b></span><span class="idx flip">J<b>&#9824;&#xFE0E;</b></span><div class="art face-art" role="img" aria-label="Line-art jack with staff"></div></div>
  <div class="card spades"><span class="idx">10<b>&#9824;&#xFE0E;</b></span><span class="idx flip">10<b>&#9824;&#xFE0E;</b></span><div class="pips r10"><i>&#9824;&#xFE0E;</i><i>&#9824;&#xFE0E;</i><i>&#9824;&#xFE0E;</i><i>&#9824;&#xFE0E;</i><i>&#9824;&#xFE0E;</i><i>&#9824;&#xFE0E;</i><i>&#9824;&#xFE0E;</i><i>&#9824;&#xFE0E;</i><i>&#9824;&#xFE0E;</i><i>&#9824;&#xFE0E;</i></div></div>
  <div class="card spades"><span class="idx">9<b>&#9824;&#xFE0E;</b></span><span class="idx flip">9<b>&#9824;&#xFE0E;</b></span><div class="pips r9"><i>&#9824;&#xFE0E;</i><i>&#9824;&#xFE0E;</i><i>&#9824;&#xFE0E;</i><i>&#9824;&#xFE0E;</i><i>&#9824;&#xFE0E;</i><i>&#9824;&#xFE0E;</i><i>&#9824;&#xFE0E;</i><i>&#9824;&#xFE0E;</i><i>&#9824;&#xFE0E;</i></div></div>
  <div class="card spades"><span class="idx">8<b>&#9824;&#xFE0E;</b></span><span class="idx flip">8<b>&#9824;&#xFE0E;</b></span><div class="pips r8"><i>&#9824;&#xFE0E;</i><i>&#9824;&#xFE0E;</i><i>&#9824;&#xFE0E;</i><i>&#9824;&#xFE0E;</i><i>&#9824;&#xFE0E;</i><i>&#9824;&#xFE0E;</i><i>&#9824;&#xFE0E;</i><i>&#9824;&#xFE0E;</i></div></div>
  <div class="card spades"><span class="idx">7<b>&#9824;&#xFE0E;</b></span><span class="idx flip">7<b>&#9824;&#xFE0E;</b></span><div class="pips r7"><i>&#9824;&#xFE0E;</i><i>&#9824;&#xFE0E;</i><i>&#9824;&#xFE0E;</i><i>&#9824;&#xFE0E;</i><i>&#9824;&#xFE0E;</i><i>&#9824;&#xFE0E;</i><i>&#9824;&#xFE0E;</i></div></div>
  <div class="card spades"><span class="idx">6<b>&#9824;&#xFE0E;</b></span><span class="idx flip">6<b>&#9824;&#xFE0E;</b></span><div class="pips r6"><i>&#9824;&#xFE0E;</i><i>&#9824;&#xFE0E;</i><i>&#9824;&#xFE0E;</i><i>&#9824;&#xFE0E;</i><i>&#9824;&#xFE0E;</i><i>&#9824;&#xFE0E;</i></div></div>
  <div class="card spades"><span class="idx">5<b>&#9824;&#xFE0E;</b></span><span class="idx flip">5<b>&#9824;&#xFE0E;</b></span><div class="pips r5"><i>&#9824;&#xFE0E;</i><i>&#9824;&#xFE0E;</i><i>&#9824;&#xFE0E;</i><i>&#9824;&#xFE0E;</i><i>&#9824;&#xFE0E;</i></div></div>
  <div class="card spades"><span class="idx">4<b>&#9824;&#xFE0E;</b></span><span class="idx flip">4<b>&#9824;&#xFE0E;</b></span><div class="pips r4"><i>&#9824;&#xFE0E;</i><i>&#9824;&#xFE0E;</i><i>&#9824;&#xFE0E;</i><i>&#9824;&#xFE0E;</i></div></div>
  <div class="card spades"><span class="idx">3<b>&#9824;&#xFE0E;</b></span><span class="idx flip">3<b>&#9824;&#xFE0E;</b></span><div class="pips r3"><i>&#9824;&#xFE0E;</i><i>&#9824;&#xFE0E;</i><i>&#9824;&#xFE0E;</i></div></div>
  <div class="card spades"><span class="idx">2<b>&#9824;&#xFE0E;</b></span><span class="idx flip">2<b>&#9824;&#xFE0E;</b></span><div class="pips r2"><i>&#9824;&#xFE0E;</i><i>&#9824;&#xFE0E;</i></div></div>
</main>
<section class="deck deck-bottom">
  <!-- diamonds -->
  <div class="card card-back" role="img" aria-label="Gold filigree pattern card back"><span class="brand-name">KETTLEBY TWINS</span></div>
  <div class="card diamonds"><span class="idx">A<b>&#9830;&#xFE0E;</b></span><span class="idx flip">A<b>&#9830;&#xFE0E;</b></span><div class="art ace-art" role="img" aria-label="Ornate filigree diamond"></div></div>
  <div class="card diamonds"><span class="idx">K<b>&#9830;&#xFE0E;</b></span><span class="idx flip">K<b>&#9830;&#xFE0E;</b></span><div class="art face-art" role="img" aria-label="Line-art king with sword"></div></div>
  <div class="card diamonds"><span class="idx">Q<b>&#9830;&#xFE0E;</b></span><span class="idx flip">Q<b>&#9830;&#xFE0E;</b></span><div class="art face-art" role="img" aria-label="Line-art queen with flower"></div></div>
  <div class="card diamonds"><span class="idx">J<b>&#9830;&#xFE0E;</b></span><span class="idx flip">J<b>&#9830;&#xFE0E;</b></span><div class="art face-art" role="img" aria-label="Line-art jack with staff"></div></div>
  <div class="card diamonds"><span class="idx">10<b>&#9830;&#xFE0E;</b></span><span class="idx flip">10<b>&#9830;&#xFE0E;</b></span><div class="pips r10"><i>&#9830;&#xFE0E;</i><i>&#9830;&#xFE0E;</i><i>&#9830;&#xFE0E;</i><i>&#9830;&#xFE0E;</i><i>&#9830;&#xFE0E;</i><i>&#9830;&#xFE0E;</i><i>&#9830;&#xFE0E;</i><i>&#9830;&#xFE0E;</i><i>&#9830;&#xFE0E;</i><i>&#9830;&#xFE0E;</i></div></div>
  <div class="card diamonds"><span class="idx">9<b>&#9830;&#xFE0E;</b></span><span class="idx flip">9<b>&#9830;&#xFE0E;</b></span><div class="pips r9"><i>&#9830;&#xFE0E;</i><i>&#9830;&#xFE0E;</i><i>&#9830;&#xFE0E;</i><i>&#9830;&#xFE0E;</i><i>&#9830;&#xFE0E;</i><i>&#9830;&#xFE0E;</i><i>&#9830;&#xFE0E;</i><i>&#9830;&#xFE0E;</i><i>&#9830;&#xFE0E;</i></div></div>
  <div class="card diamonds"><span class="idx">8<b>&#9830;&#xFE0E;</b></span><span class="idx flip">8<b>&#9830;&#xFE0E;</b></span><div class="pips r8"><i>&#9830;&#xFE0E;</i><i>&#9830;&#xFE0E;</i><i>&#9830;&#xFE0E;</i><i>&#9830;&#xFE0E;</i><i>&#9830;&#xFE0E;</i><i>&#9830;&#xFE0E;</i><i>&#9830;&#xFE0E;</i><i>&#9830;&#xFE0E;</i></div></div>
  <div class="card diamonds"><span class="idx">7<b>&#9830;&#xFE0E;</b></span><span class="idx flip">7<b>&#9830;&#xFE0E;</b></span><div class="pips r7"><i>&#9830;&#xFE0E;</i><i>&#9830;&#xFE0E;</i><i>&#9830;&#xFE0E;</i><i>&#9830;&#xFE0E;</i><i>&#9830;&#xFE0E;</i><i>&#9830;&#xFE0E;</i><i>&#9830;&#xFE0E;</i></div></div>
  <div class="card diamonds"><span class="idx">6<b>&#9830;&#xFE0E;</b></span><span class="idx flip">6<b>&#9830;&#xFE0E;</b></span><div class="pips r6"><i>&#9830;&#xFE0E;</i><i>&#9830;&#xFE0E;</i><i>&#9830;&#xFE0E;</i><i>&#9830;&#xFE0E;</i><i>&#9830;&#xFE0E;</i><i>&#9830;&#xFE0E;</i></div></div>
  <div class="card diamonds"><span class="idx">5<b>&#9830;&#xFE0E;</b></span><span class="idx flip">5<b>&#9830;&#xFE0E;</b></span><div class="pips r5"><i>&#9830;&#xFE0E;</i><i>&#9830;&#xFE0E;</i><i>&#9830;&#xFE0E;</i><i>&#9830;&#xFE0E;</i><i>&#9830;&#xFE0E;</i></div></div>
  <div class="card diamonds"><span class="idx">4<b>&#9830;&#xFE0E;</b></span><span class="idx flip">4<b>&#9830;&#xFE0E;</b></span><div class="pips r4"><i>&#9830;&#xFE0E;</i><i>&#9830;&#xFE0E;</i><i>&#9830;&#xFE0E;</i><i>&#9830;&#xFE0E;</i></div></div>
  <div class="card diamonds"><span class="idx">3<b>&#9830;&#xFE0E;</b></span><span class="idx flip">3<b>&#9830;&#xFE0E;</b></span><div class="pips r3"><i>&#9830;&#xFE0E;</i><i>&#9830;&#xFE0E;</i><i>&#9830;&#xFE0E;</i></div></div>
  <div class="card diamonds"><span class="idx">2<b>&#9830;&#xFE0E;</b></span><span class="idx flip">2<b>&#9830;&#xFE0E;</b></span><div class="pips r2"><i>&#9830;&#xFE0E;</i><i>&#9830;&#xFE0E;</i></div></div>
  <!-- clubs -->
  <div class="card joker-gold"><span class="joker-label">JOKER</span><span class="joker-label flip">JOKER</span><div class="art joker-art" role="img" aria-label="Gold jester hat illustration"></div></div>
  <div class="card clubs"><span class="idx">A<b>&#9827;&#xFE0E;</b></span><span class="idx flip">A<b>&#9827;&#xFE0E;</b></span><div class="art ace-art" role="img" aria-label="Ornate filigree club"></div></div>
  <div class="card clubs"><span class="idx">K<b>&#9827;&#xFE0E;</b></span><span class="idx flip">K<b>&#9827;&#xFE0E;</b></span><div class="art face-art" role="img" aria-label="Line-art king with sword"></div></div>
  <div class="card clubs"><span class="idx">Q<b>&#9827;&#xFE0E;</b></span><span class="idx flip">Q<b>&#9827;&#xFE0E;</b></span><div class="art face-art" role="img" aria-label="Line-art queen with flower"></div></div>
  <div class="card clubs"><span class="idx">J<b>&#9827;&#xFE0E;</b></span><span class="idx flip">J<b>&#9827;&#xFE0E;</b></span><div class="art face-art" role="img" aria-label="Line-art jack with staff"></div></div>
  <div class="card clubs"><span class="idx">10<b>&#9827;&#xFE0E;</b></span><span class="idx flip">10<b>&#9827;&#xFE0E;</b></span><div class="pips r10"><i>&#9827;&#xFE0E;</i><i>&#9827;&#xFE0E;</i><i>&#9827;&#xFE0E;</i><i>&#9827;&#xFE0E;</i><i>&#9827;&#xFE0E;</i><i>&#9827;&#xFE0E;</i><i>&#9827;&#xFE0E;</i><i>&#9827;&#xFE0E;</i><i>&#9827;&#xFE0E;</i><i>&#9827;&#xFE0E;</i></div></div>
  <div class="card clubs"><span class="idx">9<b>&#9827;&#xFE0E;</b></span><span class="idx flip">9<b>&#9827;&#xFE0E;</b></span><div class="pips r9"><i>&#9827;&#xFE0E;</i><i>&#9827;&#xFE0E;</i><i>&#9827;&#xFE0E;</i><i>&#9827;&#xFE0E;</i><i>&#9827;&#xFE0E;</i><i>&#9827;&#xFE0E;</i><i>&#9827;&#xFE0E;</i><i>&#9827;&#xFE0E;</i><i>&#9827;&#xFE0E;</i></div></div>
  <div class="card clubs"><span class="idx">8<b>&#9827;&#xFE0E;</b></span><span class="idx flip">8<b>&#9827;&#xFE0E;</b></span><div class="pips r8"><i>&#9827;&#xFE0E;</i><i>&#9827;&#xFE0E;</i><i>&#9827;&#xFE0E;</i><i>&#9827;&#xFE0E;</i><i>&#9827;&#xFE0E;</i><i>&#9827;&#xFE0E;</i><i>&#9827;&#xFE0E;</i><i>&#9827;&#xFE0E;</i></div></div>
  <div class="card clubs"><span class="idx">7<b>&#9827;&#xFE0E;</b></span><span class="idx flip">7<b>&#9827;&#xFE0E;</b></span><div class="pips r7"><i>&#9827;&#xFE0E;</i><i>&#9827;&#xFE0E;</i><i>&#9827;&#xFE0E;</i><i>&#9827;&#xFE0E;</i><i>&#9827;&#xFE0E;</i><i>&#9827;&#xFE0E;</i><i>&#9827;&#xFE0E;</i></div></div>
  <div class="card clubs"><span class="idx">6<b>&#9827;&#xFE0E;</b></span><span class="idx flip">6<b>&#9827;&#xFE0E;</b></span><div class="pips r6"><i>&#9827;&#xFE0E;</i><i>&#9827;&#xFE0E;</i><i>&#9827;&#xFE0E;</i><i>&#9827;&#xFE0E;</i><i>&#9827;&#xFE0E;</i><i>&#9827;&#xFE0E;</i></div></div>
  <div class="card clubs"><span class="idx">5<b>&#9827;&#xFE0E;</b></span><span class="idx flip">5<b>&#9827;&#xFE0E;</b></span><div class="pips r5"><i>&#9827;&#xFE0E;</i><i>&#9827;&#xFE0E;</i><i>&#9827;&#xFE0E;</i><i>&#9827;&#xFE0E;</i><i>&#9827;&#xFE0E;</i></div></div>
  <div class="card clubs"><span class="idx">4<b>&#9827;&#xFE0E;</b></span><span class="idx flip">4<b>&#9827;&#xFE0E;</b></span><div class="pips r4"><i>&#9827;&#xFE0E;</i><i>&#9827;&#xFE0E;</i><i>&#9827;&#xFE0E;</i><i>&#9827;&#xFE0E;</i></div></div>
  <div class="card clubs"><span class="idx">3<b>&#9827;&#xFE0E;</b></span><span class="idx flip">3<b>&#9827;&#xFE0E;</b></span><div class="pips r3"><i>&#9827;&#xFE0E;</i><i>&#9827;&#xFE0E;</i><i>&#9827;&#xFE0E;</i></div></div>
  <div class="card clubs"><span class="idx">2<b>&#9827;&#xFE0E;</b></span><span class="idx flip">2<b>&#9827;&#xFE0E;</b></span><div class="pips r2"><i>&#9827;&#xFE0E;</i><i>&#9827;&#xFE0E;</i></div></div>
</section>
</body>
</html>
```